Private lender of mortgages and rent to own housing

need a website that reflects real estate especially mortgage lending and rent to own houses..
Sections as follows
Home About Types of mortgages Rent to own Contact us
Target Market(s)
consumers who require non traditonal mortgages
Industry/Entity Type
Mortgage
Coding
Coded - Design and coding required
Number of Pages Required
4 page
Font styles to use
Sans Serif
Colors
Designer to choose colors to be used in the design.
Requirements
Must have
- background pictures on pages. with nice picture on homepage of houses or a community
Nice to have
- contact us form i supplied a ink to

```html
<!DOCTYPE html>
<html lang="en">
<head>
<meta charset="utf-8">
<title>Harborline Lending Group</title>
<link href="https://fonts.googleapis.com/css2?family=Open+Sans:ital,wght@0,400;0,600;0,700;0,800;1,400&display=swap" rel="stylesheet">
<style>
:root{
  --navy:#22205e;
  --orange:#f7890f;
  --text:#4a4a4a;
  --muted:#666;
  --grey:#f3f3f3;
  --line:#dedede;
  --white:#fff;
}
*{box-sizing:border-box;margin:0;padding:0}
html,body{width:678px;height:1200px;overflow:hidden}
body{font-family:"Open Sans",Arial,sans-serif;color:var(--text);background:var(--white);position:relative}
a{color:inherit;text-decoration:none}

.site-header{height:58px;display:flex;align-items:center;justify-content:space-between;padding:0 42px 0 43px}
.brand{font-size:7.5px;font-weight:700;color:var(--navy);letter-spacing:.1px;margin-top:10px}
.main-nav{display:flex;gap:21px;font-size:7px;font-weight:600;color:#444;letter-spacing:.3px}
.main-nav a.active{color:var(--navy);font-weight:700}

.hero{position:relative;height:307px;background:linear-gradient(180deg,#4f86c9 0%,#8fb5dc 30%,#9aa8b8 55%,#6f8f55 78%,#3f7a2c 100%);text-align:center;color:var(--white)}
.hero-title{padding-top:125px;font-size:25px;font-weight:800;letter-spacing:.5px;text-shadow:0 1px 4px rgba(0,0,0,.45)}
.hero-sub{font-size:11.5px;font-weight:600;margin-top:1px;text-shadow:0 1px 3px rgba(0,0,0,.5)}
.btn{display:inline-block;background:var(--orange);color:var(--white);font-size:7.5px;font-weight:700;letter-spacing:.3px;width:85px;height:25px;line-height:25px;text-align:center}
.hero .btn{margin-top:14px}
.hero-dots{position:absolute;left:0;right:0;top:338px;top:280px;display:flex;justify-content:center;gap:6px}
.hero-dots span{width:6px;height:6px;border-radius:50%;background:var(--white)}
.hero-dots span:first-child{background:transparent;border:1.5px solid var(--white)}

.section-title{color:var(--navy);font-size:13px;font-weight:700;letter-spacing:.4px;text-align:center}
.lead{font-size:7.6px;line-height:14.5px;text-align:center;color:var(--text)}

.welcome{height:190px;padding:40px 42px 0;text-align:center}
.welcome .lead{margin-top:9px}
.welcome .btn{margin-top:15px}

.rent-own{position:relative;height:340px;padding:40px 43px 0}
.rent-own::before{content:"";position:absolute;left:0;right:0;top:0;height:250px;background:var(--grey);border-radius:50% 50% 0 0/12px 12px 0 0}
.rent-own > *{position:relative}
.rent-own .lead{margin-top:9px}
.cards{display:flex;gap:17px;margin-top:21px}
.card{flex:1;height:165px;background:var(--white);border:2px solid #e6e6e6;text-align:center;padding:14px 10px 0}
.card svg{width:40px;height:40px;display:block;margin:0 auto}
.card h3{color:var(--orange);font-size:8px;font-weight:700;letter-spacing:.3px;margin-top:12px}
.card p{font-size:7.6px;line-height:13px;color:var(--text);margin-top:3px;height:56px}
.card .more{display:block;font-size:7px;font-weight:700;color:var(--navy);margin-top:9px}

.testimonials{height:190px;padding:22px 43px 0;position:relative}
.quotes{display:flex;align-items:flex-start;margin-top:20px;padding:0 10px}
.quote{display:flex;gap:18px;width:270px}
.quote + .quote{margin-left:0}
.avatar{flex:0 0 80px;height:80px;border-radius:50%;background:linear-gradient(160deg,#dcdfe3,#9aa3ad)}
.quote blockquote{font-size:7.6px;font-style:italic;line-height:13px;color:var(--text)}
.quote cite{display:block;font-style:normal;color:var(--orange);font-size:7px;font-weight:700;margin-top:7px}
.arrow{position:absolute;top:110px}
.arrow.prev{left:52px}.arrow.next{right:52px}

.site-footer{position:absolute;left:0;right:0;top:1066px;height:134px;background:var(--grey);border-radius:50% 50% 0 0/8px 8px 0 0;display:flex;padding:27px 43px 0}
.foot-col{font-size:7.2px;line-height:13.5px;color:var(--muted)}
.foot-col h4{font-size:8px;font-weight:700;color:var(--navy);letter-spacing:.3px;margin-bottom:4px}
.foot-brand{width:158px;padding-top:24px}
.foot-brand .brand{margin:0 0 14px;font-size:7.5px}
.foot-brand p{font-size:6.6px;line-height:11px}
.foot-map{width:146px}
.foot-contact{width:153px}
.contact-line{display:flex;gap:10px;align-items:center;margin-top:3px}
.signup{display:flex;width:136px;height:22px;border:1px solid #ccc;background:var(--white);margin-top:4px}
.signup span{flex:1;font-size:7px;color:#444;line-height:20px;padding-left:8px}
.signup b{width:23px;background:var(--orange);display:flex;align-items:center;justify-content:center}
.social{display:flex;gap:11px;margin-top:18px}
.social span{width:11px;height:11px;border-radius:50%;background:#555}
</style>
</head>
<body>

<header class="site-header">
  <div class="brand">HARBORLINE LENDING GROUP</div>
  <nav class="main-nav">
    <a class="active" href="#">HOME</a><a href="#">ABOUT</a><a href="#">TYPES OF MORTGAGES</a><a href="#">RENT TO OWN</a><a href="#">CONTACT US</a>
  </nav>
</header>

<section class="hero" role="img" aria-label="Photo of a sunny suburban street lined with two-storey family houses, lawns and young trees">
  <h1 class="hero-title">HARBORLINE LENDING GROUP</h1>
  <p class="hero-sub">We provide mortgage lending and rent to own houses</p>
  <a class="btn" href="#">READ MORE</a>
  <div class="hero-dots"><span></span><span></span><span></span><span></span></div>
</section>

<section class="welcome">
  <h2 class="section-title">WELCOME TO OUR WEBSITE</h2>
  <p class="lead">Aliquam molestie, mi et imperdiet euismod, dui purus auctor tellus, et interdum lacus lectus et ante. Sed accumsan sollicitudin sapien, sit amet adipiscing turpis gravida ac. In congue, neque ac lobortis volutpat, libero mauris varius mi, vitae suscipit ipsum ligula vitae risus. Duis aliquam nibh a dui iaculis viverra id a velit. Vivamus egestas risus in magna varius commodo. Sed semper viverra egestas.</p>
  <a class="btn" href="#">READ MORE</a>
</section>

<section class="rent-own">
  <h2 class="section-title">RENT TO OWN A HOME – WE CAN PUT YOU IN YOUR OWN HOME TODAY</h2>
  <p class="lead">We know life sometimes delivers challenges and it can be hard to get back on track once you have dealt with challenges. Maybe you have been through a divorce, bankruptcy, consumer propospal, loss of job, work place injury, new to the country, self-employed or some credit related challenges that have you behind the eight ball? Are these challenges making it difficult to get a mortgage? None of these things has to bind you to a lifetime of renting.</p>
  <div class="cards">
    <article class="card">
      <svg viewBox="0 0 40 40"><text x="20" y="36" text-anchor="middle" font-family="Open Sans,Arial,sans-serif" font-size="42" font-weight="600" fill="#666">$</text></svg>
      <h3>DOWN PAYMENT</h3>
      <p>We require a minimum down payment of $10,000 or 3.5% to 4% of total price of the home ..</p>
      <a class="more" href="#">READ MORE »</a>
    </article>
    <article class="card">
      <svg viewBox="0 0 40 40"><path d="M3 20 20 5l17 15h-5v16H8V20z" fill="#666"/><circle cx="20" cy="25" r="7" fill="#fff"/><circle cx="20" cy="25" r="4.5" fill="#666"/><rect x="2" y="37" width="36" height="2" fill="#666"/></svg>
      <h3>HOUSEHOLD INCOME</h3>
      <p>Steady, provable household income that can support the price of the home you would like.</p>
      <a class="more" href="#">READ MORE »</a>
    </article>
    <article class="card">
      <svg viewBox="0 0 40 40"><path d="M9 2h16l8 8v28H9z" fill="#666"/><path d="M25 2v8h8z" fill="#999"/><rect x="14" y="18" width="14" height="2.5" fill="#fff"/><rect x="14" y="24" width="14" height="2.5" fill="#fff"/><rect x="14" y="30" width="14" height="2.5" fill="#fff"/></svg>
      <h3>CREDIT REPORT</h3>
      <p>Although your credit won't necessarily disqualify you from our rent to own program..</p>
      <a class="more" href="#">READ MORE »</a>
    </article>
    <article class="card">
      <svg viewBox="0 0 40 40"><path d="M14 14 26 3l12 11h-3v10H17V14z" fill="#666"/><rect x="24" y="17" width="4" height="7" fill="#fff"/><path d="M2 24h6v13H2zM9 26c6-2 12-1 17 1 2 1 1 4-1 4h-7 9l8-4c2-1 4 1 2 3l-11 7H9z" fill="#666"/></svg>
      <h3>SELECTING A HOUSE</h3>
      <p>May not seem like a strong determining factor overall for qualifying for rent to own but it is for us.</p>
      <a class="more" href="#">READ MORE »</a>
    </article>
  </div>
</section>

<section class="testimonials">
  <h2 class="section-title">TESTIMONIALS</h2>
  <svg class="arrow prev" width="10" height="16" viewBox="0 0 10 16"><path d="M8 2 2 8l6 6" stroke="#22205e" stroke-width="2.5" fill="none"/></svg>
  <svg class="arrow next" width="10" height="16" viewBox="0 0 10 16"><path d="M2 2l6 6-6 6" stroke="#22205e" stroke-width="2.5" fill="none"/></svg>
  <div class="quotes">
    <figure class="quote">
      <div class="avatar" role="img" aria-label="Portrait photo of a smiling older client in a suit"></div>
      <div>
        <blockquote>“ Aliquam molestie, mi et imperdiet euismod, dui purus auctor tellus, et interdum lacus lectus accumsan sollicitudin sapien, sit amet adipiscing turpis gravida ac...”</blockquote>
        <cite>-NAME HEADING</cite>
      </div>
    </figure>
    <figure class="quote">
      <div class="avatar" role="img" aria-label="Portrait photo of a smiling young client"></div>
      <div>
        <blockquote>“ Aliquam molestie, mi et imperdiet euismod, dui purus auctor tellus, et interdum lacus lectus accumsan sollicitudin sapien, sit amet adipiscing turpis gravida ac...”</blockquote>
        <cite>-NAME HEADING</cite>
      </div>
    </figure>
  </div>
</section>

<footer class="site-footer">
  <div class="foot-col foot-brand">
    <div class="brand">HARBORLINE LENDING GROUP</div>
    <p>Copyright © 2017. Company Name.<br>All Right Reserved</p>
  </div>
  <div class="foot-col foot-map">
    <h4>SITE MAP</h4>
    Home<br>About<br>Types of mortgages<br>Rent to own<br>Contact us
  </div>
  <div class="foot-col foot-contact">
    <h4>CONTACT ADDRESS</h4>
    412 Ashgrove Lane,<br>Fairholm, FH2 7KT
    <div class="contact-line"><svg width="8" height="8" viewBox="0 0 8 8"><path d="M1 1h2l1 2-1 1c1 1 1 1 2 2l1-1 2 1v2C4 8 0 4 1 1z" fill="#444"/></svg><span>1-800-555-0142</span></div>
    <div class="contact-line"><svg width="8" height="7" viewBox="0 0 8 7"><rect width="8" height="7" fill="#444"/><path d="M0 0l4 4 4-4" stroke="#fff" fill="none"/></svg><span>hello@harborlinelending.com</span></div>
  </div>
  <div class="foot-col foot-signup">
    <h4>EMAIL SIGN UP</h4>
    <div class="signup"><span>Enter Email Address</span><b><svg width="8" height="12" viewBox="0 0 8 12"><path d="M1 1l5 5-5 5" stroke="#fff" stroke-width="2" fill="none"/></svg></b></div>
    <div class="social"><span></span><span></span><span></span><span></span><span></span></div>
  </div>
</footer>

</body>
</html>
```